Business Card Design

I give lessons and clinics for dressage riders
I would like the design to be an outline (with broad lines) of a dressage horse and rider with in background of whole card with print over top tan or parchment card with burgundy print

Industry/Entity Type

Business

Contact Information for Business Card

Dale Ferrin
612-374-2059
Classical dressage training for the modern American
Clinics, lessons, training level -Prix St. George

Requirements
Must have
• broad lined outline of dressage horse and rider

```html
<!DOCTYPE html>
<html lang="en">
<head>
<meta charset="utf-8">
<title>Dale Ferrin — Business Card</title>
<link rel="stylesheet" href="https://fonts.googleapis.com/css2?family=Arimo:wght@400&display=swap">
<style>
  :root {
    --page-bg: #e8e8e8;
    --card-burgundy: #43121c;
    --figure-tone: #6a2430;
    --figure-tone-deep: #5a1c27;
    --card-band: #ffffff;
    --card-text: #f4eeee;
  }
  html, body {
    margin: 0;
    padding: 0;
    width: 1200px;
    height: 864px;
    overflow: hidden;
    background: var(--page-bg);
  }
  .business-card {
    position: absolute;
    left: 100px;
    top: 146px;
    width: 1000px;
    height: 572px;
    background: var(--card-band);
    box-shadow: 0 18px 40px rgba(0, 0, 0, 0.18);
    overflow: hidden;
  }
  .card-face {
    position: absolute;
    left: 0;
    top: 0;
    width: 1000px;
    height: 532px;
    background: var(--card-burgundy);
    overflow: hidden;
  }
  .rider-illustration {
    position: absolute;
    left: 34px;
    top: 22px;
    width: 396px;
    height: 510px;
    border-radius: 120px 160px 0 0;
    background: linear-gradient(170deg, var(--figure-tone) 0%, var(--figure-tone-deep) 100%);
  }
  .card-details {
    position: absolute;
    left: 470px;
    top: 150px;
    width: 420px;
    text-align: center;
    color: var(--card-text);
    font-family: "Arimo", Arial, sans-serif;
  }
  .trainer-name {
    margin: 0;
    font-size: 32px;
    font-weight: 400;
    line-height: 1.1;
  }
  .trainer-phone {
    margin: 2px 0 0;
    font-size: 20px;
  }
  .tagline {
    margin: 40px 0 0;
    font-size: 21px;
    line-height: 1.1;
  }
  .service-list {
    list-style: none;
    margin: 16px 0 0;
    padding: 0;
    font-size: 21px;
  }
  .service-list li {
    margin-bottom: 12px;
  }
</style>
</head>
<body>
  <div class="business-card">
    <div class="card-face">
      <div class="rider-illustration" role="img" aria-label="Broad-lined outline of a dressage horse and rider in a muted burgundy tone"></div>
      <div class="card-details">
        <h1 class="trainer-name">Dale Ferrin</h1>
        <p class="trainer-phone">612-374-2059</p>
        <p class="tagline">Classical dressage training for the<br>modern American Clinics</p>
        <ul class="service-list">
          <li>lessons</li>
          <li>training level</li>
          <li>Prix St. George</li>
        </ul>
      </div>
    </div>
  </div>
</body>
</html>
```